Business card design for international hub site

I need a business card design with the logo attached. Although the site is for the teenage audience (it is about the high school graduation ball, the Prom), the business card is for professional use to be given to professional contacts (B2B), such as suppliers and partners, so it needs to look professional (but also girly, glamours and clean).

Target Market(s)

B2B

Industry/Entity Type

Media

Colors
eea4c8
f9d9e8
e667a6
9d9d9d
1b1b1b

Requirements
Must have
• Space for Name, Tile, Address, Phone, email and website.
Should not have
• Photo

```html
<!DOCTYPE html>
<html lang="en">
<head>
<meta charset="utf-8">
<title>Velvet Dance — Business Card</title>
<link rel="stylesheet" href="https://fonts.googleapis.com/css2?family=Arimo:wght@400;700&display=swap">
<style>
  :root {
    --pink-soft: #f9d9e8;
    --pink-mid: #eea4c8;
    --pink-bright: #e667a6;
    --magenta: #c81e7a;
    --orchid: #b0248a;
    --grey: #9d9d9d;
    --ink: #1b1b1b;
    --text: #555555;
    --paper: #ffffff;
    --stage: #2a2a2a;
  }
  * { box-sizing: border-box; margin: 0; padding: 0; }
  html, body { width: 1200px; height: 997px; overflow: hidden; }
  body {
    background: var(--stage);
    font-family: "Arimo", Arial, sans-serif;
    display: flex;
    flex-direction: column;
    align-items: center;
    justify-content: center;
    gap: 50px;
  }
  .card {
    position: relative;
    width: 700px;
    height: 400px;
    border-radius: 22px;
    overflow: hidden;
    background: var(--paper);
  }

  /* Front */
  .card--front .bloom-area {
    position: absolute;
    inset: 0;
    background:
      radial-gradient(ellipse 36% 60% at 18% 55%, var(--orchid) 0%, rgba(176,36,138,.75) 45%, rgba(238,164,200,0) 100%),
      radial-gradient(ellipse 30% 30% at 45% 12%, rgba(200,30,122,.9) 0%, rgba(238,164,200,0) 100%),
      radial-gradient(ellipse 35% 40% at 38% 85%, rgba(176,36,138,.9) 0%, rgba(238,164,200,0) 100%),
      linear-gradient(110deg, var(--pink-mid) 0%, var(--pink-soft) 50%, var(--paper) 80%);
  }
  .card--front .brand {
    position: absolute;
    right: 58px;
    top: 120px;
    text-align: right;
  }
  .card--front .brand__name { font-size: 44px; }

  /* Brand name */
  .brand__name {
    font-family: "Arimo", Arial, sans-serif;
    font-weight: 400;
    line-height: .95;
    color: var(--grey);
    letter-spacing: 1px;
  }

  /* Back */
  .card--back .bloom-area {
    position: absolute;
    inset: 0;
    background:
      radial-gradient(ellipse 22% 30% at 30% 10%, var(--magenta) 0%, rgba(200,30,122,0) 100%),
      radial-gradient(ellipse 25% 25% at 62% 8%, var(--orchid) 0%, rgba(176,36,138,0) 100%),
      radial-gradient(ellipse 24% 50% at 88% 45%, var(--orchid) 0%, rgba(176,36,138,.7) 45%, rgba(176,36,138,0) 100%),
      linear-gradient(175deg, var(--pink-mid) 0%, var(--pink-soft) 40%, var(--paper) 75%);
  }
  .card--back .brand {
    position: absolute;
    left: 34px;
    top: 84px;
  }
  .card--back .brand__name { font-size: 36px; }

  .contact {
    position: absolute;
    left: 36px;
    bottom: 34px;
  }
  .contact__name {
    font-weight: 700;
    font-size: 19px;
    color: var(--magenta);
    letter-spacing: .5px;
  }
  .contact__title {
    font-size: 14px;
    color: var(--grey);
    margin-bottom: 16px;
  }
  .contact__list { list-style: none; }
  .contact__item {
    display: flex;
    align-items: flex-start;
    gap: 10px;
    font-size: 15px;
    line-height: 1.2;
    color: var(--text);
    margin-top: 6px;
  }
  .contact__icon { flex: 0 0 18px; width: 18px; height: 18px; }
  .website {
    position: absolute;
    right: 30px;
    bottom: 30px;
    font-weight: 700;
    font-size: 17px;
    color: var(--magenta);
  }
</style>
</head>
<body>

  <section class="card card--front" aria-label="Card front">
    <div class="bloom-area" role="img" aria-label="Photograph of magenta orchids over a soft pink bokeh background"></div>
    <div class="brand"><p class="brand__name">velvet<br>dance</p></div>
  </section>

  <section class="card card--back" aria-label="Card back">
    <div class="bloom-area" role="img" aria-label="Photograph of magenta orchids along the top and right edge on pink bokeh"></div>
    <div class="brand"><p class="brand__name">velvet<br>dance</p></div>

    <div class="contact">
      <p class="contact__name">LENA MARSH</p>
      <p class="contact__title">Marketing Director</p>
      <ul class="contact__list">
        <li class="contact__item">
          <svg class="contact__icon" viewBox="0 0 18 18"><circle cx="9" cy="9" r="9" fill="var(--magenta)"/><path d="M5 6.5h8v5H5z" fill="#fff"/><path d="M6 6.5c0-2 6-2 6 0" stroke="#fff" stroke-width="1.2" fill="none"/></svg>
          (800) 555-0142
        </li>
        <li class="contact__item">
          <svg class="contact__icon" viewBox="0 0 18 18"><circle cx="9" cy="9" r="9" fill="var(--magenta)"/><rect x="6" y="4" width="6" height="10" rx="1" fill="#fff"/></svg>
          (555) 555-0187
        </li>
        <li class="contact__item">
          <svg class="contact__icon" viewBox="0 0 18 18"><circle cx="9" cy="9" r="9" fill="var(--magenta)"/><rect x="4.5" y="6" width="9" height="6" fill="#fff"/><path d="M4.5 6l4.5 3.5L13.5 6" stroke="var(--magenta)" stroke-width="1" fill="none"/></svg>
          lmarsh@orbitalnote.com
        </li>
        <li class="contact__item">
          <svg class="contact__icon" viewBox="0 0 18 18"><circle cx="9" cy="9" r="9" fill="var(--magenta)"/><path d="M9 14s-3.5-3.8-3.5-6.2a3.5 3.5 0 0 1 7 0C12.5 10.2 9 14 9 14z" fill="#fff"/><circle cx="9" cy="7.8" r="1.2" fill="var(--magenta)"/></svg>
          <span>48 Willow Court, 2nd Floor<br>Marlow, GA 30000</span>
        </li>
      </ul>
    </div>

    <p class="website">www.orbitalnote.com</p>
  </section>

</body>
</html>
```